Design material for Lumora Event

We need a design of POSM for Lumora Event
1. Content:
- The Lumora Event 3rd
- Singapore 28.10.2018
- A placeholder for insert logo of sponsors (limit 10 logo)
2. POSM:
- Backdrop: 5,5m and 2,6m
- Banner: 4m and 0,5m
- Standee: 0,8m and 2m
- Cover: A4 size
3. Style:
We need style simply because we are a hospital.
Main color: light blue and a little of green (if can)

Hope to see your design soon!

Font styles to use
Sans Serif

Colors
0792cd
85cae6
86cfc6
33b8a4
33a6d7

```html
<!DOCTYPE html>
<html lang="en">
<head>
<meta charset="utf-8">
<title>3rd Lumora Event · Singapore 2018</title>
<link rel="stylesheet" href="https://fonts.googleapis.com/css2?family=Montserrat:wght@300;400;500;700&display=swap">
<style>
  :root {
    --blue-deep: #0792cd;
    --blue-soft: #85cae6;
    --blue-mid: #33a6d7;
    --teal-soft: #86cfc6;
    --teal: #33b8a4;
    --navy-title: #1a618f;
    --ink: #222222;
    --body-grey: #555555;
    --paper-center: #ffffff;
    --paper-edge: #e4e4e5;
  }
  * { margin: 0; padding: 0; box-sizing: border-box; }
  html, body { width: 849px; height: 1200px; overflow: hidden; }
  body { font-family: "Montserrat", Arial, sans-serif; }
  .cover {
    position: relative;
    width: 849px;
    height: 1200px;
    overflow: hidden;
    background: radial-gradient(ellipse at 50% 40%, var(--paper-center) 0%, #f3f3f4 45%, var(--paper-edge) 100%);
  }
  .site-url {
    position: absolute; top: 43px; left: 0; width: 100%;
    text-align: center; font-size: 22px; font-weight: 400;
    color: var(--teal-soft); letter-spacing: 0.3px;
  }
  .icon-ring { position: absolute; left: 105px; top: 145px; width: 655px; height: 655px; }
  .edition {
    position: absolute; top: 277px; left: 0; width: 100%;
    text-align: center; color: var(--teal-soft); font-weight: 300;
    font-size: 120px; line-height: 1;
  }
  .edition sup { font-size: 24px; vertical-align: 0; position: relative; left: 3px; }
  .event-title {
    position: absolute; top: 380px; left: 0; width: 100%;
    text-align: center; color: var(--navy-title); font-weight: 300;
    font-size: 88px; line-height: 89px; letter-spacing: 0.5px;
  }
  .city {
    position: absolute; top: 570px; left: 0; width: 100%;
    text-align: center; color: var(--teal); font-weight: 400;
    font-size: 28px; letter-spacing: 15px; padding-left: 15px;
  }
  .year {
    position: absolute; top: 617px; left: 0; width: 100%;
    text-align: center; color: var(--ink); font-weight: 400; font-size: 36px;
  }
  .date-block { position: absolute; top: 856px; left: 0; width: 100%; height: 90px; }
  .date-block .day {
    position: absolute; right: 479px; top: 4px; text-align: right;
    color: var(--teal); font-weight: 400; line-height: 1;
  }
  .day .weekday { display: block; font-size: 46px; }
  .day .month { display: block; font-size: 34px; margin-top: 4px; }
  .date-block .date-number {
    position: absolute; left: 390px; top: -6px;
    font-size: 100px; font-weight: 300; line-height: 1; color: var(--blue-mid);
  }
  .date-block .time {
    position: absolute; left: 513px; top: 8px;
    font-size: 36px; font-weight: 400; line-height: 1; color: var(--blue-deep);
  }
  .date-block .venue {
    position: absolute; left: 516px; top: 56px;
    font-size: 23px; font-weight: 400; color: var(--blue-deep);
  }
  .intro {
    position: absolute; top: 979px; left: 76px; width: 694px;
    font-size: 13.2px; line-height: 18.5px; color: var(--body-grey);
    text-align: justify; text-align-last: center; font-weight: 400;
    hyphens: auto;
  }
  .contact { position: absolute; top: 1054px; left: 0; width: 100%; text-align: center; color: var(--ink); }
  .contact .label { display: block; font-size: 7.5px; font-weight: 500; letter-spacing: 0.3px; }
  .contact .email { display: block; font-size: 14px; margin-top: 3px; }
  .sponsors {
    position: absolute; left: 0; bottom: 0; width: 100%; height: 104px;
    background: #ffffff;
    display: flex; align-items: center; justify-content: space-between;
    padding: 0 40px 4px;
  }
  .sponsor {
    font-size: 12px; font-weight: 700; color: var(--ink);
    letter-spacing: 0.2px; white-space: nowrap;
  }
</style>
</head>
<body>
<main class="cover">
  <p class="site-url">LumoraEvent.com</p>

  <svg class="icon-ring" viewBox="0 0 660 660" role="img" aria-label="Ring of outlined science and study icons: flasks, books, ruler, magnifier, calculator, globe, lightbulb, monitor, pie chart and stars">
    <defs>
      <radialGradient id="ring-fade" cx="50%" cy="50%" r="50%">
        <stop offset="64%" stop-color="#ececed"/>
        <stop offset="82%" stop-color="#dcdddf"/>
        <stop offset="100%" stop-color="#e8e8e9"/>
      </radialGradient>
    </defs>
    <path fill="url(#ring-fade)" fill-rule="evenodd"
      d="M330 0 A330 330 0 1 1 329.9 0 Z M330 118 A212 212 0 1 0 330.1 118 Z"/>
  </svg>

  <div class="edition">3<sup>rd</sup></div>
  <h1 class="event-title">Lumora<br>Event</h1>
  <p class="city">SINGAPORE</p>
  <p class="year">2018</p>

  <section class="date-block">
    <div class="day"><span class="weekday">SUNDAY</span><span class="month">OCTOBER</span></div>
    <div class="date-number">28</div>
    <div class="time">6:30pm</div>
    <div class="venue">Local: Lorem ipsum</div>
  </section>

  <p class="intro">At vero eos et accusamus et iusto odio dignissimos ducimus qui blanditiis praesentium voluptatum deleniti atque corrupti quos dolores et quas molestias excepturi sint occaecati cupiditate non provident, similique sunt in culpa qui officia deserunt mollitia animi, id est laborum et dolorum fuga.</p>

  <div class="contact">
    <span class="label">QUESTIONS? CONTACT</span>
    <span class="email">LumoraEvent@email.com</span>
  </div>

  <footer class="sponsors">
    <span class="sponsor">Solvane</span>
    <span class="sponsor">Quillon</span>
    <span class="sponsor">Amberhill</span>
    <span class="sponsor">Northpeak</span>
    <span class="sponsor">Gildmoor</span>
    <span class="sponsor">Tessaro</span>
    <span class="sponsor">Orchida</span>
    <span class="sponsor">Kestrel Row</span>
    <span class="sponsor">Halcyon</span>
    <span class="sponsor">Dunmere</span>
  </footer>
</main>
</body>
</html>
```